Telecommunications/Power civil contractor needs business card design

Were a new telecommunications/power underground civil contractor that is looking for a new business card design. Our company colours are silver or grey and orange. Feel free to use the white background logo or the black background logo.

Target Market(s)

Local contractors, utility companies, private sector mining/energy companies, developers.

Industry/Entity Type

Telecommunications

Contact Information for Business Card

Each card will need the following info:
Persons name:
Title:
E-mail:
Phone number:
Shop Address:
Mailing Address:

Requirements
Must have
• Each card will need the following info:
• Persons name:
• Title:
• E-mail:
• Phone number:
• Shop Address:
• Mailing Address:

```html
<!DOCTYPE html>
<html lang="en">
<head>
<meta charset="utf-8">
<title>Ridgeline Conduit Inc — Business Card</title>
<link rel="stylesheet" href="https://fonts.googleapis.com/css2?family=Roboto:wght@400;700&display=swap">
<style>
  :root {
    --bg: #e9e6e1;
    --orange: #f26a2e;
    --orange-deep: #e85a22;
    --grey: #6d6e71;
    --silver: #a7a9ac;
    --white: #ffffff;
    --ink: #4a4b4d;
  }
  * { box-sizing: border-box; margin: 0; padding: 0; }
  html, body {
    width: 1200px; height: 950px; overflow: hidden;
    background: var(--bg);
    font-family: "Roboto", Arial, sans-serif;
  }
  .canvas {
    position: relative; width: 1200px; height: 950px;
  }
  .card {
    position: absolute; left: 300px;
    width: 600px; height: 343px;
    border-radius: 4px;
    box-shadow: 0 6px 18px rgba(0,0,0,0.18);
  }
  /* Front */
  .card-front {
    top: 90px; background: var(--white);
    display: flex; flex-direction: column; align-items: center; justify-content: center; gap: 18px;
  }
  .brand-dot {
    width: 96px; height: 96px; border-radius: 50%;
    border: 8px solid var(--silver);
  }
  .brand-name {
    font-weight: 700; font-size: 30px; letter-spacing: 1px;
    color: var(--orange); text-transform: uppercase; text-align: center; line-height: 1.1;
  }
  /* Back */
  .card-back {
    top: 517px;
    background: linear-gradient(135deg, var(--orange) 0%, var(--orange-deep) 100%);
    color: var(--white);
  }
  .back-mark {
    position: absolute; left: 60px; top: 96px; width: 160px;
    display: flex; flex-direction: column; align-items: center; gap: 12px;
  }
  .back-mark .brand-dot { width: 110px; height: 110px; border-color: var(--white); }
  .back-mark .brand-name { color: var(--white); font-size: 15px; }
  .divider {
    position: absolute; left: 262px; top: 40px; width: 1px; height: 263px;
    background: rgba(255,255,255,0.55);
  }
  .details {
    position: absolute; left: 290px; top: 58px;
    font-size: 15px; letter-spacing: 0.4px; text-transform: uppercase;
  }
  .person-name { font-weight: 700; font-size: 22px; letter-spacing: 0.6px; }
  .person-title { margin-top: 2px; font-size: 15px; }
  .address { margin-top: 22px; line-height: 1.35; }
  .contacts { margin-top: 16px; list-style: none; }
  .contacts li { display: flex; align-items: center; gap: 12px; line-height: 1.55; }
  .contacts svg { width: 15px; height: 15px; flex: none; }
</style>
</head>
<body>
<main class="canvas">
  <section class="card card-front">
    <div class="brand-dot"></div>
    <div class="brand-name">Ridgeline Conduit Inc</div>
  </section>

  <section class="card card-back">
    <div class="back-mark">
      <div class="brand-dot"></div>
      <div class="brand-name">Ridgeline</div>
    </div>
    <div class="divider"></div>
    <div class="details">
      <div class="person-name">Marcus Hale</div>
      <div class="person-title">President</div>
      <div class="address">4127 Alder Creek Road<br>Millbrook, NY 12545</div>
      <ul class="contacts">
        <li>
          <svg viewBox="0 0 16 16" aria-hidden="true"><path fill="#fff" d="M3.2 1.5l2.3 2.8-1.3 1.6c.9 2 2.4 3.6 4.4 4.6l1.6-1.3 2.8 2.3-1.2 2.3C6.9 13.9 2.1 9.1 1 4.2z"/></svg>
          555 0142 7781
        </li>
        <li>
          <svg viewBox="0 0 16 16" aria-hidden="true"><rect x="1.5" y="3.5" width="13" height="9" fill="none" stroke="#fff" stroke-width="1.4"/><path d="M1.5 3.5 8 9l6.5-5.5" fill="none" stroke="#fff" stroke-width="1.4"/></svg>
          marcus@example.com
        </li>
        <li>
          <svg viewBox="0 0 16 16" aria-hidden="true"><circle cx="8" cy="8" r="6.3" fill="none" stroke="#fff" stroke-width="1.4"/><ellipse cx="8" cy="8" rx="2.6" ry="6.3" fill="none" stroke="#fff" stroke-width="1.2"/><path d="M1.8 8h12.4" stroke="#fff" stroke-width="1.2"/></svg>
          www.example.com
        </li>
      </ul>
    </div>
  </section>
</main>
</body>
</html>
```